Harbor Lantern's Chinese/Dim Sum Restaurant Menu

Harbor Lantern's is a seafood-asian fusion restaurant featuring dim sum and other classical asian fusion items.

We need a menu design that includes both our food menu and our drink menu.

Food menu: Needs to have space for descriptions of food (please just include a place holder and we will input them later). See attached for food menu items.

Drink menu: Just lists of items with prices. See attached Jade Meadow Menu- please include the same items, but rebrand for Harbor Lantern's.

The menus must be able to be printed in a 4.25x11in paper.

We want something modern and contemporary. My boss likes geometrical design aspects and minimalism. So, nothing too ornate. But, it has to be different from the Jade Meadow menus. Colors can be black, red, gold or blue- but it must be able to be tied into our black and red Harbor Lantern's logo. Including elements of Chinese culture, especially fishing, is a plus, but not necessary.

We also need this in ai format when we download final copy so we can edit in the future.

UPDATE: Please note, we already have a logo.

Target Market(s)

Upscale family diners

Industry/Entity Type

Chinese Food

Font styles to use
Serif
Sans Serif

Colors
0054AA
0677BA
7BADD7
CADEEF
E8F1F8
0094D4
00A9DD
6FCCEA
C7EBF8
E9F6FB
FFC000
F8CF3A
FAE287
FDF2CF
FEFAEE
EB3D1F
EC4F4E
F09395
F8D3D4
FCEDEE

Requirements
Must have
• Classic, minimalist, elegant

```html
<!DOCTYPE html>
<html lang="en">
<head>
<meta charset="utf-8">
<title>Harbor Lantern's – Food and Drink Menu</title>
<link href="https://fonts.googleapis.com/css2?family=Oswald:wght@500;600;700&family=Montserrat:wght@500;600;700;900&family=Poppins:wght@400;500;600&display=swap" rel="stylesheet">
<style>
:root{
  --backdrop:#6b6a79;
  --paper-light:#f6f6f6;
  --paper-dark:#e4e4e4;
  --red:#e1261c;
  --ink:#111111;
  --muted:#555555;
  --vegan:#3aa845;
  --spicy:#e0392b;
  --gf:#f2a81d;
}
*{margin:0;padding:0;box-sizing:border-box}
html,body{width:762px;height:1200px;overflow:hidden;background:var(--backdrop)}
.canvas{position:relative;width:762px;height:1200px}
.panel{position:absolute;width:202px;height:522px;overflow:hidden;
  background:linear-gradient(160deg,var(--paper-light),var(--paper-dark));
  font-family:"Poppins",sans-serif;color:var(--ink)}
.p-cover{left:56px;top:65px}
.p-food{left:279px;top:65px}
.p-sweets{left:504px;top:65px}
.p-liquor{left:56px;top:614px}
.p-wine{left:279px;top:614px}
.p-beer{left:504px;top:614px}
.abs{position:absolute}
.photo{position:absolute}
.red-band{position:absolute;background:var(--red)}

.tag{position:absolute;height:14px;background:var(--red);color:#fff;
  font-family:"Oswald",sans-serif;font-weight:600;font-size:8.5px;line-height:14px;
  padding-left:9px;letter-spacing:.3px;
  clip-path:polygon(4px 0,100% 0,calc(100% - 4px) 100%,0 100%)}

.list{position:absolute;display:flex;flex-direction:column}
.row{display:flex;align-items:center;height:var(--step,7.25px);font-size:4.3px;white-space:nowrap}
.row .lead{flex:1;height:0;border-bottom:.5px solid var(--red);margin:0 2px;opacity:.8}
.price{display:inline-block;width:18px;height:5.4px;line-height:5.4px;text-align:center;
  background:var(--ink);color:#fff;font-size:3.6px;font-weight:600}
.price.hot{background:var(--red)}
.price.sm{width:11px}
.ic{display:inline-block;width:3.4px;height:3.4px;border-radius:50%;margin-left:.8px;vertical-align:middle}
.ic.v{background:var(--vegan)}.ic.s{background:var(--spicy)}.ic.g{background:var(--gf)}
.caps .row{font-family:"Montserrat",sans-serif;font-weight:600;font-size:4px}

.brand{position:absolute;left:0;width:202px;top:34px;text-align:center;
  font-family:"Montserrat",sans-serif;font-weight:700;font-size:10px;letter-spacing:.3px;color:var(--ink)}
.brand-dot{position:absolute;left:93px;top:16px;width:16px;height:16px;border-radius:50%;background:var(--red)}
.cover-kicker{position:absolute;left:0;width:202px;top:80px;text-align:center;
  font-family:"Oswald",sans-serif;font-weight:700;font-size:25px;color:var(--red);letter-spacing:-.3px;line-height:1.1}
.cover-title{position:absolute;left:0;width:202px;top:106px;text-align:center;
  font-family:"Montserrat",sans-serif;font-weight:900;font-size:52px;line-height:1;letter-spacing:-1px}
.hh-title{position:absolute;left:0;width:202px;top:297px;text-align:center;
  font-family:"Oswald",sans-serif;font-weight:500;font-size:15px;line-height:1.2}
.hh-time{position:absolute;left:0;width:202px;top:318px;text-align:center;
  font-family:"Montserrat",sans-serif;font-weight:700;font-size:8.5px;line-height:10px;color:var(--red)}
.rule{position:absolute;height:1px;background:var(--ink)}
.rule.red{background:var(--red)}
.hh-sub{position:absolute;left:0;width:202px;top:355px;text-align:center;
  font-family:"Oswald",sans-serif;font-weight:700;font-size:21px;line-height:1.2}
.deal{position:absolute;left:0;width:202px;top:395px;text-align:center;
  font-family:"Montserrat",sans-serif;font-weight:700;font-size:8.6px;line-height:10px}
.deal em{font-style:normal;color:var(--red)}
.fine{position:absolute;left:0;width:202px;top:425px;text-align:center;
  font-family:"Poppins",sans-serif;font-size:6.4px;letter-spacing:1.4px;line-height:9px}
.disclaimer{position:absolute;left:18px;width:166px;top:477px;text-align:center;font-size:4.5px;line-height:6.3px}

.drinks-title{position:absolute;left:11px;top:274px;font-family:"Oswald",sans-serif;font-weight:600;font-size:23px}
.na{position:absolute;font-family:"Montserrat",sans-serif;font-weight:600;font-size:3.9px;line-height:4.6px}
.na .accent{color:var(--red);font-weight:700}
.na small{display:block;font-weight:400;font-size:3.4px}
.desc{display:block;font-family:"Poppins",sans-serif;font-weight:400;font-size:3.3px;line-height:3.9px;color:var(--muted)}
.legend{position:absolute;left:11px;top:411px;width:178px;height:15px;border:.8px solid var(--ink);border-radius:2px;
  display:flex;align-items:center;font-size:4.2px}
.legend span{flex:1;display:flex;align-items:center;justify-content:center;gap:3px}
.legend span+span{border-left:.8px solid var(--red)}
.legend .ic{width:6px;height:6px}

.col{position:absolute;font-family:"Montserrat",sans-serif;font-weight:600;font-size:4.3px;line-height:6.7px}
.col h3{font-weight:700;font-size:6.6px;line-height:8.5px}
.col .sub{font-weight:500;font-size:3.5px;line-height:5.3px;padding-left:6px;position:relative}
.col .sub::before{content:"";position:absolute;left:1.5px;top:1.6px;width:2.4px;height:2.4px;border-radius:50%;background:var(--red)}
.col .cat{font-size:4.3px}

.label-sm{position:absolute;font-family:"Montserrat",sans-serif;font-size:3.9px;font-weight:500}
.heading-sm{position:absolute;font-family:"Montserrat",sans-serif;font-weight:700;font-size:6.4px}
.wine .row{font-family:"Montserrat",sans-serif;font-weight:500;font-size:4.2px;--step:7.9px}
.tripled{display:flex;gap:3px}
.entry{position:absolute;left:11px;width:180px;display:flex;align-items:flex-start;font-family:"Montserrat",sans-serif;font-weight:600;font-size:4.1px}
.entry .txt{flex:1}
</style>
</head>
<body>
<main class="canvas">

  <!-- COVER -->
  <section class="panel p-cover">
    <span class="brand-dot"></span>
    <div class="brand">HARBOR LANTERN'S</div>
    <div class="cover-kicker">FOOD AND DRINK</div>
    <div class="cover-title">MENU</div>
    <div class="red-band" style="left:0;top:170px;width:202px;height:80px;transform:skewY(-4deg)"></div>
    <div class="photo" role="img" aria-label="Pan-fried dumplings on a black plate with noodles and shrimp salad"
      style="left:0;top:168px;width:202px;height:88px;background:radial-gradient(ellipse at 50% 50%,#c9a57a 0%,#7a5a3a 35%,#2a2420 60%,rgba(200,110,60,.9) 85%);border-radius:40px 40px 30px 30px"></div>
    <div class="hh-title">HAPPY HOUR APPETIZERS*</div>
    <div class="hh-time">EVERYDAY<br>3 PM – 6 PM</div>
    <div class="rule" style="left:12px;top:353px;width:178px"></div>
    <div class="hh-sub">DRINK &amp; APPETIZERS</div>
    <div class="deal">$5 <em>WELL LIQUORS</em><br>$1 OFF <em>ALL ALCOHOLIC BEVERAGES</em></div>
    <div class="fine">*AVAILABLE ONLY IN THE BAR,<br>DINE IN ONLY</div>
    <div class="rule red" style="left:11px;top:469px;width:182px"></div>
    <p class="disclaimer">JADE MEADOW RESTAURANT RESERVES THE RIGHT TO CHANGE MENU SELECTIONS, AND/OR THE PRICES THAT ACCOMPANY THOSE ITEMS, AS THEY APPEAR ON THE MENUS AT THE RESTAURANT. ONLY ONE PROMOTION/SPECIAL/DISCOUNT/KICKBACK USED AT A TIME, PER TABLE OR CHECK.</p>
  </section>

  <!-- FOOD -->
  <section class="panel p-food">
    <div class="tag" style="left:11px;top:12px;width:67px">DIM SUM</div>
    <div class="list" style="left:14px;top:31px;width:125px">
      <div class="row">Potsticker<span class="lead"></span><span class="price">$12</span></div>
      <div class="row">Meatless Dumpling<span class="ic v"></span><span class="lead"></span><span class="price">$11</span></div>
      <div class="row">Lobster Dumpling<span class="lead"></span><span class="price">$13</span></div>
      <div class="row">Sticky Rice<span class="lead"></span><span class="price">$5</span></div>
      <div class="row">Pork Siu Mai<span class="lead"></span><span class="price">$12</span></div>
      <div class="row">Spicy Won Ton<span class="ic s"></span><span class="lead"></span><span class="price">$12</span></div>
      <div class="row">Vegan Spicy Won Ton<span class="ic v"></span><span class="ic s"></span><span class="lead"></span><span class="price">$12</span></div>
      <div class="row">Pork Xie Long Boa<span class="lead"></span><span class="price">$11</span></div>
      <div class="row">Crab &amp; Pork Xie Long Bao<span class="lead"></span><span class="price">$12</span></div>
      <div class="row">BBQ Pork Bao<span class="lead"></span><span class="price">$10</span></div>
      <div class="row">Sweet Corn Dumpling<span class="ic v"></span><span class="lead"></span><span class="price">$11</span></div>
    </div>
    <div class="photo" role="img" aria-label="Row of dumplings on a black slate with chopsticks"
      style="left:146px;top:22px;width:52px;height:93px;background:linear-gradient(170deg,#3a3a3a,#1c1c1c);transform:rotate(-6deg);border-radius:3px"></div>

    <div class="tag" style="left:63px;top:119px;width:68px">SOUP</div>
    <div class="photo" role="img" aria-label="Bowl of hot and sour soup" style="left:4px;top:124px;width:58px;height:48px;border-radius:50%;background:radial-gradient(circle,#c9803a 0%,#a85a25 45%,#f4f1ec 52%,#d8d4cf 100%)"></div>
    <div class="list" style="left:66px;top:137px;width:122px">
      <div class="row">Cup Hot &amp; Sour Soup<span class="ic s"></span><span class="lead"></span><span class="price">$5</span></div>
      <div class="row">Bowl Hot &amp; Sour Soup<span class="ic s"></span><span class="lead"></span><span class="price">$8</span></div>
      <div class="row">Cup Egg Flower Soup<span class="lead"></span><span class="price">$5</span></div>
      <div class="row">Bowl Egg Flower Soup<span class="lead"></span><span class="price">$8</span></div>
      <div class="row">Bowl Pork Wonton Soup<span class="lead"></span><span class="price">$9</span></div>
    </div>

    <div class="tag" style="left:11px;top:180px;width:67px">APPETIZERS</div>
    <div class="photo" role="img" aria-label="Plate of stir-fried noodles with chopsticks" style="left:130px;top:180px;width:72px;height:45px;border-radius:50%;background:radial-gradient(ellipse,#d79a3c 0%,#b5702a 50%,#efece8 70%,rgba(230,230,230,0) 72%)"></div>
    <div class="list" style="left:14px;top:198px;width:119px">
      <div class="row">Walnut Shrimp Warp<span class="ic g"></span><span class="lead"></span><span class="price">$12</span></div>
      <div class="row">Chicken Lettuce Warp<span class="lead"></span><span class="price">$12</span></div>
      <div class="row">Tofu Lettuce Warp<span class="ic v"></span><span class="lead"></span><span class="price">$12</span></div>
      <div class="row">Curry Mussels + add Noodles ($3)<span class="lead"></span><span class="price">$15</span></div>
      <div class="row">Seabass Roll<span class="lead"></span><span class="price">$12</span></div>
      <div class="row">Crab Cheese Wonton<span class="lead"></span><span class="price">$10</span></div>
    </div>
    <div class="photo" role="img" aria-label="Sliced wraps filled with vegetables" style="left:0;top:245px;width:68px;height:48px;border-radius:10px;background:linear-gradient(135deg,#d9c29a,#8b9a4a 50%,#4a3a2a)"></div>
    <div class="list" style="left:71px;top:244px;width:117px">
      <div class="row">Tuna Tower<span class="lead"></span><span class="price">$23</span></div>
      <div class="row">Ahi Tuna and Fish Chips<span class="lead"></span><span class="price">$21</span></div>
      <div class="row">Edamame<span class="ic v"></span><span class="ic g"></span><span class="lead"></span><span class="price">$7</span></div>
      <div class="row">Sesame Soy Noodle Salad(cold)<span class="ic v"></span><span class="lead"></span><span class="price">$8</span></div>
      <div class="row">Chinese Pancake<span class="ic v"></span><span class="lead"></span><span class="price">$9</span></div>
      <div class="row">Garlic Cucumber Salad<span class="ic v"></span><span class="lead"></span><span class="price">$11</span></div>
      <div class="row">Seaweed Salad<span class="ic v"></span><span class="lead"></span><span class="price">$10</span></div>
    </div>

    <div class="tag" style="left:11px;top:302px;width:67px">SAUTEED</div>
    <div class="list" style="left:14px;top:323px;width:174px">
      <div class="row">Szechuan Seabass<span class="lead"></span><span class="price">$18</span></div>
      <div class="row">Seabass Black Bean Sauce<span class="lead"></span><span class="price">$18</span></div>
      <div class="row">Kung Po Shrimp<span class="ic g"></span><span class="ic s"></span><span class="lead"></span><span class="price">$20</span></div>
      <div class="row">Kung Po Chicken<span class="ic g"></span><span class="lead"></span><span class="price">$18</span></div>
      <div class="row">Kung Po Tofu<span class="ic g"></span><span class="ic s"></span><span class="ic v"></span><span class="lead"></span><span class="price">$18</span></div>
      <div class="row">Broccoli Chicken<span class="lead"></span><span class="price">$18</span></div>
      <div class="row">Broccoli Beef<span class="lead"></span><span class="price">$19</span></div>
      <div class="row">Broccoli Shrimp<span class="ic g"></span><span class="lead"></span><span class="price">$20</span></div>
      <div class="row">Mongolian Beef<span class="ic g"></span><span class="lead"></span><span class="price">$20</span></div>
      <div class="row">General Ng's Chicken<span class="ic s"></span><span class="lead"></span><span class="price">$18</span></div>
      <div class="row">General Ng's Tofu<span class="ic s"></span><span class="ic v"></span><span class="lead"></span><span class="price">$18</span></div>
    </div>
    <div class="legend">
      <span><i class="ic v"></i>VEGAN</span>
      <span><i class="ic s"></i>SPICY</span>
      <span><i class="ic g"></i>GLUTEN FREE</span>
    </div>
    <div class="red-band" style="left:0;top:455px;width:202px;height:70px;transform:skewY(-8deg)"></div>
    <div class="photo" role="img" aria-label="Stone pot of kimchi stew and a plate of noodles lifted with chopsticks"
      style="left:0;top:440px;width:202px;height:82px;background:radial-gradient(ellipse at 25% 60%,#e06a2a 0%,#1e1a18 40%,rgba(0,0,0,0) 55%),radial-gradient(ellipse at 78% 70%,#b98a4e 0%,#8a6a3f 35%,rgba(0,0,0,0) 55%)"></div>
  </section>

  <!-- SWEETS & NA DRINKS -->
  <section class="panel p-sweets">
    <div class="tag" style="left:11px;top:12px;width:67px">VEGGIE</div>
    <div class="photo" role="img" aria-label="Scattered vegetables and herbs" style="left:162px;top:0;width:40px;height:60px;background:radial-gradient(circle at 60% 40%,#e0402a 0%,#5a9a3a 30%,rgba(0,0,0,0) 60%)"></div>
    <div class="list" style="left:12px;top:31px;width:178px">
      <div class="row">Sauteed Green Beans<span class="ic v"></span><span class="ic g"></span><span class="lead"></span><span class="price">$16</span></div>
      <div class="row">Iceberg Lettuce with "Oyster" Sauce<span class="ic v"></span><span class="lead"></span><span class="price">$14</span></div>
      <div class="row">Broccoli Garlic Sauce<span class="ic v"></span><span class="ic g"></span><span class="lead"></span><span class="price">$15</span></div>
    </div>

    <div class="tag" style="left:11px;top:61px;width:94px">RICE &amp; NOODLES</div>
    <div class="list" style="left:12px;top:77px;width:114px">
      <div class="row">Seafood Fried Rice<span class="lead"></span><span class="price">$18</span></div>
      <div class="row">Veggie Fried Rice<span class="lead"></span><span class="price">$14</span></div>
      <div class="row">Chicken Fried Rice<span class="lead"></span><span class="price">$15</span></div>
      <div class="row">Beef Fried Rice<span class="lead"></span><span class="price">$16</span></div>
      <div class="row">Seafood Chow Mein<span class="lead"></span><span class="price">$18</span></div>
      <div class="row">Chicken Chow Mein<span class="lead"></span><span class="price">$16</span></div>
      <div class="row">Beef Chow Mein<span class="lead"></span><span class="price">$7</span></div>
    </div>
    <div class="photo" role="img" aria-label="Plate of fried rice with shrimp and carrots" style="left:128px;top:80px;width:74px;height:40px;border-radius:50%;background:radial-gradient(ellipse,#d8b060 0%,#c8893a 40%,#f2f0ec 62%,rgba(230,230,230,0) 70%)"></div>

    <div class="photo" role="img" aria-label="Steamed buns on a wooden board" style="left:0;top:127px;width:67px;height:55px;border-radius:6px;background:radial-gradient(circle at 50% 40%,#f6f3ee 0%,#e9e2d6 40%,#b9874e 75%)"></div>
    <div class="tag" style="left:64px;top:137px;width:96px">SWEET &amp; DESSERT</div>
    <div class="list" style="left:70px;top:157px;width:120px">
      <div class="row">Chocolate Dumpling<span class="lead"></span><span class="price">$10</span></div>
      <div class="row">Sweet Egg Bao<span class="lead"></span><span class="price">$9</span></div>
      <div class="row">Walnut Bao<span class="lead"></span><span class="price">$9</span></div>
    </div>

    <div class="tag" style="left:11px;top:191px;width:72px">DESSERTS</div>
    <div class="photo" role="img" aria-label="Slice of layered cake with a cherry on top" style="left:130px;top:185px;width:72px;height:100px;background:linear-gradient(160deg,rgba(0,0,0,0) 20%,#f3eee8 30%,#b8343a 55%,#f3eee8 70%,rgba(0,0,0,0) 85%)"></div>
    <div class="caps">
      <div class="list" style="left:12px;top:208px;width:116px;--step:6px">
        <div class="row">PURE DECADENCE<span class="lead"></span><span class="price">$9</span></div>
      </div>
      <div class="abs" style="left:12px;top:214px;font-size:3.5px;line-height:4.3px">Molten Chocolate Lava Cake,<br>Pineapple Coconut Ice Cream,<br>Whipped Cream</div>
      <div class="list" style="left:12px;top:229px;width:116px;--step:8.5px">
        <div class="row">CHEESECAKE<span class="lead"></span><span class="price">$8</span></div>
        <div class="row">PINEAPPLE COCONUT ICE CREAM<span class="lead"></span><span class="price">$7</span></div>
        <div class="row">SALTED CARAMEL ICE CREAM<span class="lead"></span><span class="price">$7</span></div>
        <div class="row">MARIONBERRY SORBET<span class="lead"></span><span class="price">$6</span></div>
        <div class="row">VANILLA ICE CREAM<span class="lead"></span><span class="price">$6</span></div>
      </div>
    </div>

    <div class="drinks-title">DRINKS</div>
    <div class="photo" role="img" aria-label="Glasses of lemonade with lime and mint" style="left:2px;top:310px;width:87px;height:60px;background:radial-gradient(ellipse at 50% 55%,#f0e27a 0%,#d9c94a 35%,#6aa94a 55%,rgba(0,0,0,0) 70%)"></div>
    <div class="tag" style="left:90px;top:312px;width:81px">NA BEVERAGES</div>
    <div class="na" style="left:93px;top:331px">
      <span class="accent">BOTTOMLESS</span><br>CROWN COLA,<br>DIET CROWN,<br>CROWN ZERO<br>TONIC<br>UNSWEETENED<br>ICED TEA
    </div>
    <div class="na" style="left:146px;top:336px">SPRITZ LIME<br>BARLOW'S ROOT BEER<br>DR. PEPPERTON<br>GINGER ALE<br>LEMONADE</div>
    <span class="price abs" style="left:146px;top:362px">$3</span>
    <div class="caps">
      <div class="list" style="left:12px;top:381px;width:178px;--step:6px"><div class="row">APPLE, ORANGE, CRANBERRY,<span class="lead"></span><span class="price">$3</span></div></div>
      <div class="na" style="left:12px;top:387px">GRAPEFRUIT, PINEAPPLE,<br>CHOCOLATE MILK, MILK<small>(NO REFILLS)</small></div>
      <div class="list" style="left:12px;top:408px;width:178px;--step:6px"><div class="row">VIRGIN PINA COLADA &amp;<span class="lead"></span><span class="price">$4.5</span></div></div>
      <div class="na" style="left:12px;top:414px">VIRGIN STRAWBERRY DAQUIRI<small>(SHAKEN – NO REFILLS)</small></div>
      <div class="list" style="left:12px;top:429px;width:178px;--step:6px"><div class="row">STRAWBERRY LEMONADE, CHERRY<span class="lead"></span><span class="price">$4</span></div></div>
      <div class="na" style="left:12px;top:435px">GINGER FIZZ, COLA CHERRY FIZZ<small>(LIMIT ONE REFILL)</small></div>
    </div>
    <div class="red-band" style="left:0;top:460px;width:202px;height:62px;transform:skewY(-6deg)"></div>
    <div class="photo" role="img" aria-label="Row of colourful fruit cocktails garnished with citrus slices"
      style="left:0;top:452px;width:202px;height:70px;background:linear-gradient(90deg,#e8782a,#f0a23a 25%,#d94a2a 40%,#2a6ad9 58%,#e0b03a 75%,#f2e6b0)"></div>
  </section>

  <!-- LIQUOR -->
  <section class="panel p-liquor">
    <div class="tag" style="left:10px;top:12px;width:68px">LIQUOR</div>
    <div class="col" style="left:13px;top:31px;width:90px">
      <h3>VODKA</h3>
      <div>NORDHAVN</div><div>VISTULA</div><div>TIDECOVE CLEARWATER</div><div>SILVER HERON</div><div>KUMO VODKA</div><div>KETTLE MARK</div><div>NEW HARBOR VODKA</div><div>STOLVANA</div><div>TAVINS</div><div>DEEP CURRENT</div>
      <div class="sub">CRANBERRY</div><div class="sub">GRAPEFRUIT</div><div class="sub">LEMON</div><div class="sub">ORANGE</div><div class="sub">PEACH</div><div class="sub">SWEET TEA</div>
      <div>SUMMITRY</div><div class="sub">CITRUS</div>
      <h3>WHISKEY</h3>
      <div>BRASSWORKS HOUSE BLEND</div><div>JED DANVERS</div><div>SEABRIGHT'S 7</div><div class="cat">BOURBON</div>
      <div class="sub">BASIL HARLAN'S</div><div class="sub">BASIL HARLAN'S RUBY CASK</div><div class="sub">BRACKEN'S KENTUCKY BOURBON</div><div class="sub">BRANTLEY'S</div><div class="sub">BAXTER'S BOURBON</div><div class="sub">BISON TRAIL</div><div class="sub">CEDARHALL BOURBON</div><div class="sub">FALCON RARE</div><div class="sub">HARLOW'S CREEK</div><div class="sub">JON BECKETT</div><div class="sub">KNOLL CREEK 9</div><div class="sub">KNOLL CREEK 12</div><div class="sub">MILLER'S MARK</div><div class="sub">MILLER'S MARK LIMITED CASK</div><div class="sub">THORNTON BOURBON</div><div class="sub">WELTON SPECIAL RESERVE</div><div class="sub">WILD PHEASANT</div><div class="sub">WOODVALE RESERV</div>
      <div class="cat">CANADIAN</div>
      <div class="sub">BLACK SATIN</div><div class="sub">REGAL CREST</div><div class="sub">MACNORRIE</div><div class="sub">PENDRAKE</div>
      <div class="cat">IRISH</div>
      <div class="sub">TIDECOVE HARBOR XXX</div><div class="sub">KILBRIDE</div><div class="sub">RED WREN</div>
      <div class="cat">JAPANESE</div>
      <div class="sub">HOSHI BLEND</div><div class="sub">SUNRISE KIRI</div><div class="sub">TENMARU</div>
      <div class="cat">RYE</div>
      <div class="sub">PRAIRIE PREMIUM RYE</div><div class="sub">CEDARHALL RYE</div><div class="sub">PENDRAKE RYE</div><div class="sub">SABRE RYE</div><div class="sub">ISLE BUNKHOUSE RYE</div>
      <div class="cat">SCOTCH</div>
      <div class="sub">BALMORIE TWIN CASK</div><div class="sub">CLAN MACRORY</div><div class="sub">GLENFARROW 14</div><div class="sub">GLENLARRICK 12</div><div class="sub">JAMIE WALDEN BLACK</div><div class="sub">JAMIE WALDEN RED</div>
      <div class="cat">COGNAC</div>
      <div class="sub">COURMELLE</div><div class="sub">HANLON</div><div class="sub">ORVANE</div>
    </div>
    <div class="col" style="left:105px;top:31px;width:95px">
      <h3>GIN</h3>
      <div>ALDER GIN</div><div>BAYVIEW SAPPHIRE</div><div>HENLEY'S</div><div>ROKAI GIN</div><div>TARRANT</div>
      <h3 style="margin-top:5px">TEQUILA</h3>
      <div>1850 REPOSADA</div><div>1850 SILVER</div><div>CAZADEROS</div><div>HORNILLO DARK BARREL</div><div>HORNILLO PLATA</div><div>HORNILLO REPOSADA</div><div>PATRONA</div><div>SAUVERA</div>
    </div>
    <div class="photo" role="img" aria-label="Gin and tonic with sliced limes on a wooden board" style="left:88px;top:132px;width:97px;height:72px;border-radius:8px;background:radial-gradient(ellipse at 60% 40%,#e8f3d2 0%,#a8d06a 35%,#c88a4e 70%,rgba(0,0,0,0) 80%)"></div>
    <div class="col" style="left:105px;top:216px;width:95px">
      <h3>RUM</h3>
      <div>BAHIRO GOLD</div><div>BAHIRO SUPERIOR</div><div>CAPTAIN MARLOW</div><div>CRUZERA 151</div><div>MYLAND'S DARK RUM</div><div>MALUNA COCONUT RUM</div><div>PLANTERA PINEAPPLE RUM</div>
      <h3 style="margin-top:3px">LIQUORS</h3>
      <div>BAILFORDS</div><div>CARMELI</div><div>DRAMLIN</div><div>FIREBRAND</div><div>FRANGELLA</div><div>GIRAUD PAMPLEMOUSSE</div><div>GIRAUD ORGEAT</div><div>GOLDFLAKE</div><div>JAGERWALD</div><div>KALANI</div><div>MIDORO MELON</div><div>MR DARK COFFEE</div><div>RUMPLEMINT</div><div>EMBERFIRE</div><div>ST. VERDELLE'S ELDERFLOWER</div><div>ISLE COVE DISTILLERY</div>
      <div class="sub">LOGANBERRY</div><div class="sub">BLACKBERRY</div><div class="sub">RASPBERRY</div>
    </div>
    <div class="red-band" style="left:0;top:470px;width:202px;height:52px;transform:skewY(-8deg)"></div>
    <div class="photo" role="img" aria-label="Beer bottles and glasses of beer with ice" style="left:76px;top:424px;width:126px;height:98px;background:linear-gradient(90deg,#2a1a10,#5a3a1a 20%,#d9a23a 45%,#3a2414 65%,#c98a2a 85%,#2a1a10)"></div>
  </section>

  <!-- WINE & SAKE -->
  <section class="panel p-wine wine">
    <div class="tag" style="left:11px;top:12px;width:67px">WINE</div>
    <div class="heading-sm" style="left:13px;top:28px">BOTTLE ONLY</div>
    <div class="label-sm" style="left:173px;top:31px">BOTTLE</div>
    <div class="list" style="left:14px;top:37px;width:176px">
      <div class="row">TALL CEDARS POET'S RISE RIESLING (WA)<span class="lead"></span><span class="price">$50</span></div>
      <div class="row">WHITECLIFF SAUVIGNON BLANC (NZ)<span class="lead"></span><span class="price">$45</span></div>
      <div class="row">DORSEY CELLARS HAYES CHARDONNAY (WA)<span class="lead"></span><span class="price">$60</span></div>
      <div class="row">THREE VINTNERS MERLOT (WA)<span class="lead"></span><span class="price">$50</span></div>
      <div class="row">TRYST SYRAH (WA)<span class="lead"></span><span class="price">$53</span></div>
      <div class="row">DUCKRIDGE CABERNET (WA)<span class="lead"></span><span class="price">$90</span></div>
      <div class="row">JORVALE CABERNET (CA)<span class="lead"></span><span class="price">$55</span></div>
      <div class="row">TRYST CABERNET (WA)<span class="lead"></span><span class="price">$60</span></div>
      <div class="row">ABELIA CABERNET (WA)<span class="lead"></span><span class="price">$80</span></div>
      <div class="row">PEPPERFIELD CABERNET (WA)<span class="lead"></span><span class="price">$80</span></div>
      <div class="row">DOUBLETURN CABERNET (WA)<span class="lead"></span><span class="price">$200</span></div>
      <div class="row">LORENZETTI CABERNET (WA)<span class="lead"></span><span class="price">$200</span></div>
      <div class="row">MISCHIEF MAKER RED BLEND (CA)<span class="lead"></span><span class="price">$34</span></div>
      <div class="row">FIDELIS RED BLEND (WA)<span class="lead"></span><span class="price">$35</span></div>
      <div class="row">MATHESON CHALKBOARD RED (WA)<span class="lead"></span><span class="price">$50</span></div>
      <div class="row">DELORME D3 RED BLEND (WA)<span class="lead"></span><span class="price">$80</span></div>
      <div class="row">QUILL CREEK RED BLEND (WA)<span class="lead"></span><span class="price">$100</span></div>
    </div>
    <div class="label-sm" style="left:152px;top:175px">GLASS/BOTTLE</div>
    <div class="list" style="left:14px;top:182px;width:176px">
      <div class="row">RYAN PORTER RIESLING (WA)<span class="lead"></span><span class="tripled"><span class="price sm">$11</span><span class="price sm hot">$16</span><span class="price">$40</span></span></div>
      <div class="row">AERIALIST PINOT GRIS (OR)<span class="lead"></span><span class="tripled"><span class="price sm">$11</span><span class="price sm hot">$16</span><span class="price">$40</span></span></div>
      <div class="row">BRANCROFT SAUV BLANC (NZ)<span class="lead"></span><span class="tripled"><span class="price sm">$11</span><span class="price sm hot">$16</span><span class="price">$40</span></span></div>
      <div class="row">TRANCHET PALE BLANC (WA)<span class="lead"></span><span class="tripled"><span class="price sm">$11</span><span class="price sm hot">$16</span><span class="price">$40</span></span></div>
      <div class="row">DUCKRIDGE CHARDONNAY (WA)<span class="lead"></span><span class="tripled"><span class="price sm">$11</span><span class="price sm hot">$16</span><span class="price">$40</span></span></div>
      <div class="row">KENDRA JAMESON CHARDONNAY (CA)<span class="lead"></span><span class="tripled"><span class="price sm">$11</span><span class="price sm hot">$16</span><span class="price">$40</span></span></div>
    </div>
    <div class="list" style="left:14px;top:239px;width:176px">
      <div class="row">FRANCIS CORVINO PINOT NOIR (CA)<span class="lead"></span><span class="tripled"><span class="price sm">$11</span><span class="price sm hot">$16</span><span class="price">$40</span></span></div>
      <div class="row">DRUMHAVEN MERLOT (WA)<span class="lead"></span><span class="tripled"><span class="price sm">$11</span><span class="price sm hot">$16</span><span class="price">$40</span></span></div>
      <div class="row">12 HOOVES MERLOT (WA)<span class="lead"></span><span class="tripled"><span class="price sm">$11</span><span class="price sm hot">$16</span><span class="price">$40</span></span></div>
      <div class="row">TRANCHET CABERNET FRANC (WA)<span class="lead"></span><span class="tripled"><span class="price sm">$11</span><span class="price sm hot">$16</span><span class="price">$40</span></span></div>
      <div class="row">CRANE RIDGE SYRAH (WA)<span class="lead"></span><span class="tripled"><span class="price sm">$11</span><span class="price sm hot">$16</span><span class="price">$40</span></span></div>
      <div class="row">JUGGERLINE CABERNET (CA)<span class="lead"></span><span class="tripled"><span class="price sm">$11</span><span class="price sm hot">$16</span><span class="price">$40</span></span></div>
      <div class="row">12 HOOVES CABERNET (WA)<span class="lead"></span><span class="tripled"><span class="price sm">$11</span><span class="price sm hot">$16</span><span class="price">$40</span></span></div>
    </div>
    <div class="list" style="left:14px;top:302px;width:176px">
      <div class="row">TORMARELLA CALARENA ROSE (FR)<span class="lead"></span><span class="tripled"><span class="price sm">$11</span><span class="price sm hot">$16</span><span class="price">$40</span></span></div>
      <div class="row">PLUM WINE<span class="lead"></span><span class="tripled"><span class="price sm">$11</span><span class="price sm hot">$16</span><span class="price">$40</span></span></div>
      <div class="row">CHAMPAGNE SPLIT<span class="lead"></span><span class="price">$40</span></div>
      <div class="row">HOUSE WHITE<span class="lead"></span><span class="price">$40</span></div>
      <div class="row">HOUSE RED<span class="lead"></span><span class="price">$40</span></div>
    </div>
    <div class="tag" style="left:11px;top:355px;width:67px">SAKE</div>
    <div class="list" style="left:14px;top:372px;width:176px">
      <div class="row">SHIRAKUMO HOUSE SAKE<span class="lead"></span><span class="tripled"><span class="price sm" style="width:14px">SM $7</span><span class="price hot" style="width:14px">LG $10</span></span></div>
      <div class="row">TOZAN SNOW BLOSSOM NIGORI<span class="lead"></span><span class="price">$40</span></div>
      <div class="row">MOONPEARL COCONUT LEMONGRASS<span class="lead"></span><span class="price">$40</span></div>
      <div class="row">HIKARI YUZU SHU<span class="lead"></span><span class="price">$40</span></div>
    </div>
    <div class="red-band" style="left:0;top:462px;width:202px;height:60px;transform:skewY(-7deg)"></div>
    <div class="photo" role="img" aria-label="Glasses of white and red wine with grapes, cheese and a decanter"
      style="left:0;top:424px;width:202px;height:98px;background:linear-gradient(90deg,rgba(0,0,0,0) 2%,#e8d88a 14%,#5a1020 28%,#3a2a4a 45%,#6a1a2a 62%,#2a0a10 78%,rgba(0,0,0,0) 95%)"></div>
  </section>

  <!-- BEER & COCKTAILS -->
  <section class="panel p-beer">
    <div class="tag" style="left:11px;top:12px;width:83px">BOTTLED BEER</div>
    <div class="caps">
      <div class="list" style="left:11px;top:32px;width:119px;--step:8px">
        <div class="row">STELLAN CIDRE<span class="lead"></span><span class="price">$53</span></div>
        <div class="row">WHITE CREST<span class="lead"></span><span class="price">$90</span></div>
      </div>
      <div class="abs" style="left:11px;top:45.5px;font-family:Montserrat,sans-serif;font-size:3.1px;font-weight:500">BLACK CHERRY, WATERMELON, MANGO</div>
      <div class="list" style="left:11px;top:51px;width:119px;--step:7.9px">
        <div class="row">WIDMARK HEFEWEISEN<span class="lead"></span><span class="price">$55</span></div>
        <div class="row">BLUE HARVEST<span class="lead"></span><span class="price">$60</span></div>
        <div class="row">STELLAN ARTISTE<span class="lead"></span><span class="price">$80</span></div>
        <div class="row">CORONET<span class="lead"></span><span class="price">$80</span></div>
        <div class="row">GINNELL<span class="lead"></span><span class="price">$200</span></div>
        <div class="row">HEINMARK<span class="lead"></span><span class="price">$200</span></div>
        <div class="row">TSINGSHAN<span class="lead"></span><span class="price">$34</span></div>
        <div class="row">RAINMOUNT<span class="lead"></span><span class="price">$35</span></div>
        <div class="row">CORVIS LIGHT<span class="lead"></span><span class="price">$50</span></div>
      </div>
    </div>
    <div class="photo" role="img" aria-label="Two amber beer bottles" style="left:146px;top:29px;width:44px;height:92px;background:linear-gradient(90deg,rgba(0,0,0,0) 5%,#8a4a14 15%,#c8782a 30%,rgba(0,0,0,0) 45%,#8a4a14 58%,#d08a34 75%,rgba(0,0,0,0) 90%)"></div>

    <div class="tag" style="left:11px;top:130px;width:83px">COCKTAILS</div>
    <div class="entry" style="top:152px"><div class="txt">PINEAPPLE DAQUIRI<span class="desc">Plantera Pineapple Rum, Lime Juice, Rich Simple Syrup</span></div><span class="price">$50</span></div>
    <div class="entry" style="top:167.5px"><div class="txt">ELDERFLOWER GIMLET<span class="desc">Alder Gin, St. Verdelle Elderflower Liqueur, Lime Juice</span></div><span class="price">$45</span></div>
    <div class="entry" style="top:183.5px"><div class="txt">ISLE BLACKBERRY MANHATTAN<span class="desc">Miller's Mark Whiskey, 98 pt. Isle Cove Blackberry Liqueur*, Aromatic Bitters</span></div><span class="price">$60</span></div>
    <div class="entry" style="top:199.5px"><div class="txt">JACK &amp; JIN<span class="desc">Jed Danvers Whiskey, Alder Gin, Ginger Beer, Orange Bitters, Lime Juice, Rosemary Simple Syrup</span></div><span class="price">$50</span></div>
    <div class="entry" style="top:219.5px"><div class="txt">HI-YA MARGARITA<span class="desc">1850 Reposado, Triple Sec, Grand Marquis, Lime Juice, Rich Simple Syrup</span></div><span class="price">$53</span></div>
    <div class="entry" style="top:235.5px"><div class="txt">ISLE BRAMBLE<span class="desc">Alder Gin, 98 pt. Isle Cove Blackberry Liqueur*, Lemon Juice,<br>Rich Simple Syrup</span></div><span class="price">$90</span></div>
    <div class="entry" style="top:255.5px"><div class="txt">RUM PUNCH<span class="desc">Maluna Coconut Rum, White Rum, Myland's Dark Rum, Orange Juice, Pineapple Juice, Lime Juice, Grenadine</span></div><span class="price">$55</span></div>
    <div class="entry" style="top:275.5px"><div class="txt">BOURBON LEMONADE<span class="desc">Knoll Creek Bourbon, Lemon Juice, Mint, Simple Syrup</span></div><span class="price">$60</span></div>
    <div class="entry" style="top:291.5px"><div class="txt">TEQUILA SMASH<span class="desc">Hornillo Reposado, Coinvelle, Mint, Lime Juice, Lemon Juice</span></div><span class="price">$80</span></div>
    <div class="entry" style="top:307px"><div class="txt">KELVIN THE GOAT<span class="desc">Tavins Vodka, Isle Cove Raspberry Liqueur*, Ginger Beer, Fresh Lime</span></div><span class="price">$80</span></div>
    <div class="entry" style="top:323px"><div class="txt">LAVENDER LOGANBERRY LEMON DROP<span class="desc">Tidecove Vodka, 94 pt. Isle Cove Loganberry Liqueur*, Lemon Juice, Lavender<br>Simple Syrup</span></div><span class="price">$200</span></div>
    <div class="entry" style="top:342.5px"><div class="txt">NEW FASHIONED<span class="desc">Miller's Mark Whiskey, Amaretto, Simple Syrup, Orange Bitters, Cherry, Orange</span></div><span class="price">$200</span></div>
    <div class="entry" style="top:358.5px"><div class="txt">ISLE COVE BLACKBERRY MANHATTAN<span class="desc">Miller's Mark Whiskey, 98 pt. Isle Cove Blackberry Liqueur*, Aromatic Bitters</span></div><span class="price">$34</span></div>
    <div class="entry" style="top:374.5px"><div class="txt">HIBISCUS MARGARITA<span class="desc">Sauvera Tequila, Triple Sec, Hibiscus Simple Syrup, Lime Juice</span></div><span class="price">$35</span></div>
    <div class="entry" style="top:390.5px"><div class="txt">CHINATINI<span class="desc">Tidecove Vodka, Isle Cove Raspberry Liqueur*, Triple Sec, Cranberry Juice, Lemon<br>Juice, Rich Simple Syrup</span></div><span class="price">$50</span></div>
    <div class="entry" style="top:410px"><div class="txt">SPIRIT FREE – SUMMER SUNSET<span class="desc">Dhara NA Orange, Pineapple Juice, Cranberry Juice, Orange Juice</span></div><span class="price">$50</span></div>
    <div class="red-band" style="left:0;top:462px;width:202px;height:60px;transform:skewY(-7deg)"></div>
    <div class="photo" role="img" aria-label="Glasses of white and red wine with grapes, cheese and a decanter"
      style="left:0;top:424px;width:202px;height:98px;background:linear-gradient(90deg,rgba(0,0,0,0) 2%,#e8d88a 14%,#5a1020 28%,#3a2a4a 45%,#6a1a2a 62%,#2a0a10 78%,rgba(0,0,0,0) 95%)"></div>
  </section>

</main>
</body>
</html>
```